Event flyer for Sunday night Youth Group

Need a 4 x 6 or 5 x 7 flyer for a new youth group starting on April 14. The youth group is for students in middle school and high school so it needs to look fun and cool, but not childish. I prefer it not to include pictures of people unless it's so obscure you can't really see their faces. I've uploaded some pictures of flyers I like. I've also attached a couple versions of our logo to use on the flyer.
Information the flyer needs to include:
Youth Group
Sundays, 6-8pm (beginning April 14)
Location: Marlowe's - 4219 Quarry Fern Ave N, Keizer, 97318
There will be dinner, games, friends, and a message.
Target Market(s)
Youth ages 13-18
Industry/Entity Type
Church
Font styles to use
Colors
Designer to choose colors to be used in the design.
Look and feel

```html
<!DOCTYPE html>
<html lang="en">
<head>
<meta charset="utf-8">
<title>Youth Group Flyer</title>
<link rel="stylesheet" href="https://fonts.googleapis.com/css2?family=Roboto+Condensed:wght@400;500;700;800&family=Montserrat:wght@500&display=swap">
<style>
  :root {
    --navy: #1c3540;
    --sage: #86917e;
    --sage-light: #a3ac9a;
    --logo-ink: #24414d;
    --orange: #f5931d;
    --orange-deep: #ef8412;
    --white: #ffffff;
    --page: #e9e7e2;
  }
  * { margin: 0; padding: 0; box-sizing: border-box; }
  html, body { width: 1194px; height: 1200px; overflow: hidden; background: var(--page); }
  .flyer {
    position: absolute; left: 227px; top: 45px;
    width: 740px; height: 1110px;
    background: var(--navy);
    overflow: hidden;
    font-family: "Roboto Condensed", sans-serif;
    box-shadow: 0 10px 30px rgba(0,0,0,.18);
  }
  .flyer-shapes { position: absolute; inset: 0; }
  .brand {
    position: absolute; left: 150px; top: 170px;
    display: flex; flex-direction: column; align-items: center; gap: 18px;
  }
  .brand-mark { width: 70px; height: 70px; background: var(--logo-ink); }
  .brand-name {
    font-family: "Montserrat", sans-serif; font-weight: 500;
    font-size: 44px; letter-spacing: 2px; color: var(--logo-ink);
  }
  .headline { position: absolute; right: 55px; top: 340px; text-align: right; }
  .headline-youth {
    display: block;
    font-weight: 500; font-size: 110px; line-height: .9;
    color: var(--sage); letter-spacing: 2px;
  }
  .headline-group {
    display: block;
    font-weight: 800; font-size: 220px; line-height: .82;
    letter-spacing: -2px;
    background: linear-gradient(120deg, var(--orange-deep) 0%, var(--orange) 45%, #f8a12e 60%, var(--orange) 100%);
    -webkit-background-clip: text; background-clip: text; color: transparent;
  }
  .event-time {
    margin-top: 14px;
    font-weight: 700; font-size: 52px; line-height: 1; color: var(--white);
  }
  .event-start {
    margin-top: 6px;
    font-weight: 400; font-size: 30px; line-height: 1.1; color: var(--sage);
  }
  .event-start strong { font-weight: 700; }
  .details { position: absolute; left: 95px; top: 945px; width: 560px; color: var(--white); }
  .venue { font-size: 24px; line-height: 1.25; }
  .activities {
    margin-top: 12px; padding: 8px 0;
    border-top: 2px dotted rgba(255,255,255,.6);
    border-bottom: 2px dotted rgba(255,255,255,.6);
    font-size: 29px; letter-spacing: .5px; white-space: nowrap;
  }
</style>
</head>
<body>
  <main class="flyer">
    <svg class="flyer-shapes" viewBox="0 0 740 1110" aria-hidden="true">
      <path fill="var(--sage)" d="M0,100 C200,60 460,30 630,36 C735,42 752,90 705,140 C600,250 300,350 0,470 Z"/>
      <path fill="none" stroke="var(--white)" stroke-opacity=".75" stroke-width="1.5"
            d="M0,118 C210,78 460,48 625,54 C718,60 728,100 690,140 C590,244 300,352 0,458"/>
      <path fill="var(--sage)" d="M740,235 C705,258 680,290 682,318 C684,348 708,362 740,366 Z"/>
      <path fill="none" stroke="var(--sage-light)" stroke-width="1.2"
            d="M740,224 C696,250 670,286 672,318 C674,352 702,372 740,376"/>
      <path fill="var(--sage)" d="M0,885 C250,878 500,840 740,775 L740,1110 L0,1110 Z"/>
      <path fill="none" stroke="var(--white)" stroke-opacity=".8" stroke-width="1.5"
            d="M70,915 C300,902 520,862 740,805"/>
    </svg>

    <div class="brand">
      <div class="brand-mark"></div>
      <div class="brand-name">PINEWAY</div>
    </div>

    <header class="headline">
      <h1>
        <span class="headline-youth">YOUTH</span>
        <span class="headline-group">GROUP</span>
      </h1>
      <p class="event-time">SUNDAYS, 6-8PM</p>
      <p class="event-start">Beginning <strong>April 14</strong></p>
    </header>

    <section class="details">
      <p class="venue">Marlowe's - 4219<br>Quarry Fern Ave N, Keizer, 97318</p>
      <p class="activities">DINNER | GAMES | FRIENDS | MESSAGE</p>
    </section>
  </main>
</body>
</html>
```